Open sky harmony Business cards - yoga studio

We need business cards for our yoga studio Opensky Harmony.
We would like to see designs that include the colour blue and our logo.
The business card should communicate a feeling of strength and calm

Requirements
Must have
• The business card must include
"Mirela Thornquist - Director"
and
"42 Wattlecrest Avenue
Dunmoreton
VIC 3917
Ph - 0471 586 204"

```html
<!DOCTYPE html>
<html lang="en">
<head>
<meta charset="utf-8">
<title>Opensky Harmony – Business Cards</title>
<link rel="stylesheet" href="https://fonts.googleapis.com/css2?family=Ubuntu:ital,wght@0,300;0,400;0,700;1,400&display=swap">
<style>
  :root {
    --teal: #5499ab;
    --card-white: #f5f6f6;
    --backdrop: #eceeef;
    --ink-light: #ffffff;
  }
  * { box-sizing: border-box; margin: 0; padding: 0; }
  html, body {
    width: 1200px;
    height: 1017px;
    overflow: hidden;
    background: var(--backdrop);
    font-family: "Ubuntu", sans-serif;
  }
  .sheet {
    position: relative;
    width: 1200px;
    height: 1017px;
  }
  .card {
    position: absolute;
    left: 250px;
    width: 700px;
    height: 428px;
    overflow: hidden;
    box-shadow: 0 2px 10px rgba(0,0,0,0.08);
  }
  .card--front {
    top: 52px;
    background: var(--teal);
    display: flex;
    align-items: center;
    justify-content: center;
  }
  .card--back {
    top: 537px;
    background: var(--card-white);
  }
  .brand {
    display: flex;
    flex-direction: column;
    align-items: center;
    gap: 18px;
  }
  .brand__dot {
    width: 70px;
    height: 70px;
    border-radius: 50%;
    background: var(--ink-light);
  }
  .brand__name {
    font-weight: 300;
    font-size: 54px;
    letter-spacing: 1px;
    color: var(--ink-light);
    line-height: 1;
    white-space: nowrap;
  }
  .card__brand-panel {
    position: absolute;
    left: 0; top: 0;
    width: 262px;
    height: 100%;
    display: flex;
    align-items: flex-start;
    justify-content: center;
    padding: 84px 24px 0 20px;
  }
  .card__brand-panel .brand { gap: 10px; }
  .card__brand-panel .brand__dot { width: 44px; height: 44px; background: var(--teal); }
  .card__brand-panel .brand__name { font-size: 23px; letter-spacing: 0.5px; color: var(--teal); }
  .card__info-panel {
    position: absolute;
    left: 262px; top: 0;
    width: 438px;
    height: 100%;
    background: var(--teal);
    color: var(--ink-light);
    padding: 58px 44px 0 0;
    text-align: right;
  }
  .card__info-panel::before {
    content: "";
    position: absolute;
    left: -12px;
    top: 148px;
    border-top: 9px solid transparent;
    border-bottom: 9px solid transparent;
    border-right: 12px solid var(--teal);
  }
  .person__name {
    font-weight: 700;
    font-size: 30px;
    letter-spacing: 0.5px;
  }
  .person__role {
    font-style: italic;
    font-size: 21px;
    margin-top: 4px;
  }
  .contact {
    margin-top: 78px;
    list-style: none;
    font-size: 21px;
    line-height: 1.35;
  }
  .contact__item {
    display: flex;
    justify-content: flex-end;
    align-items: flex-end;
    gap: 14px;
  }
  .contact__item + .contact__item { margin-top: 10px; }
  .contact__icon { width: 16px; height: 20px; flex: none; margin-bottom: 3px; }
</style>
</head>
<body>
<main class="sheet">
  <section class="card card--front" aria-label="Business card front">
    <div class="brand">
      <span class="brand__dot" aria-hidden="true"></span>
      <span class="brand__name">Opensky Harmony</span>
    </div>
  </section>

  <section class="card card--back" aria-label="Business card back">
    <div class="card__brand-panel">
      <div class="brand">
        <span class="brand__dot" aria-hidden="true"></span>
        <span class="brand__name">Opensky Harmony</span>
      </div>
    </div>
    <div class="card__info-panel">
      <p class="person__name">Mirela Thornquist</p>
      <p class="person__role">Director</p>
      <ul class="contact">
        <li class="contact__item">
          <span>42 Wattlecrest Avenue<br>Dunmoreton VIC 3917</span>
          <svg class="contact__icon" viewBox="0 0 16 20" aria-hidden="true">
            <path d="M8 1a6 6 0 0 0-6 6c0 4.5 6 12 6 12s6-7.5 6-12a6 6 0 0 0-6-6zm0 8.5A2.5 2.5 0 1 1 8 4.5a2.5 2.5 0 0 1 0 5z" fill="#ffffff"/>
          </svg>
        </li>
        <li class="contact__item">
          <span>0471 586 204</span>
          <svg class="contact__icon" viewBox="0 0 16 20" aria-hidden="true">
            <path d="M4 2l3 3.5-2 2c1 2.5 2.8 4.5 5 5.5l2-2 3 3-2 2.5C7.5 17.5 2 11 2 4.5z" fill="#ffffff"/>
          </svg>
        </li>
      </ul>
    </div>
  </section>
</main>
</body>
</html>
```